Upmarket Dessert Lounge needs a Business Card Design

We are an upmarket dessert lounge needing a business card to match our image.

We want something that is simple yet beautiful, feminine, classy, sophisticated and elegant. We want it to stand out and don't mind if it is bold.

The design should include our logo and colours of red or maroon with gold highlights. We don't mind if black is used.

Marlow & Quince

Target Market(s)

For those who like to indulge or treat themselves and give in to their temptations on good quality desserts.

Industry/Entity Type

Business

Requirements
Must have
• Must include our logo and our name

Marlow & Quince

M & Q

```html
<!DOCTYPE html>
<html lang="en">
<head>
<meta charset="utf-8">
<title>Marlow &amp; Quince — Business Card</title>
<link rel="stylesheet" href="https://fonts.googleapis.com/css2?family=Libre+Baskerville:wght@400;700&family=PT+Sans:wght@400&display=swap">
<style>
  :root {
    --maroon: #7a1418;
    --maroon-deep: #641014;
    --gold: #f6d9a6;
    --paper: #ffffff;
    --ink: #3a3a3a;
    --rule: #b9b9b9;
    --backdrop: #ece8e3;
  }
  * { box-sizing: border-box; margin: 0; padding: 0; }
  html, body {
    width: 1200px; height: 758px; overflow: hidden;
    background: var(--backdrop);
  }
  .sheet {
    width: 1200px; height: 758px;
    display: flex; align-items: center; justify-content: center; gap: 40px;
  }
  .card {
    position: relative;
    width: 540px; height: 310px;
    border-radius: 22px;
    overflow: hidden;
    box-shadow: 0 6px 18px rgba(0,0,0,0.18);
  }

  /* Front */
  .card-front { background: var(--paper); }
  .brand {
    position: absolute; left: 30px; top: 60px; width: 220px; height: 110px;
    display: flex; align-items: center; justify-content: center;
    font-family: "Libre Baskerville", serif; font-weight: 400;
    font-size: 22px; line-height: 1.25; text-align: center;
    color: var(--maroon);
  }
  .divider {
    position: absolute; left: 268px; top: 52px; width: 1px; height: 110px;
    background: linear-gradient(var(--rule), rgba(185,185,185,0));
  }
  .contact-list {
    position: absolute; left: 284px; top: 58px; list-style: none;
    font-family: "PT Sans", sans-serif; font-size: 13.5px; color: var(--ink);
  }
  .contact-list li { display: flex; align-items: center; gap: 7px; height: 21px; }
  .contact-list svg { width: 12px; height: 12px; fill: var(--ink); flex: none; }
  .name-band {
    position: absolute; left: 0; right: 0; top: 204px; height: 50px;
    background: var(--maroon);
    display: flex; align-items: center; justify-content: center;
    color: var(--paper);
    font-family: "Libre Baskerville", serif; font-size: 15px;
  }
  .name-band .person { font-weight: 700; margin-right: 6px; letter-spacing: 0.5px; }
  .name-band .title { font-weight: 400; font-size: 13px; }
  .name-band::before {
    content: ""; position: absolute; left: 0; right: 0; top: -14px; height: 6px;
    background: var(--maroon);
  }
  .address {
    position: absolute; left: 0; right: 0; top: 266px; text-align: center;
    font-family: "PT Sans", sans-serif; font-size: 13.5px; color: var(--ink);
  }

  /* Back */
  .card-back {
    background: var(--maroon);
    display: flex; flex-direction: column; align-items: center; justify-content: center;
  }
  .monogram {
    display: flex; align-items: center; justify-content: center; gap: 16px;
    font-family: "Libre Baskerville", serif; font-weight: 400;
    font-size: 62px; color: var(--gold); line-height: 1;
    margin-top: -10px;
  }
  .monogram .dot {
    width: 12px; height: 12px; border-radius: 50%; background: var(--gold);
  }
  .site {
    margin-top: 48px;
    font-family: "PT Sans", sans-serif; font-size: 19px; letter-spacing: 2.5px;
    color: var(--paper);
  }
</style>
</head>
<body>
<main class="sheet">
  <section class="card card-front" aria-label="Card front">
    <div class="brand">Marlow &amp; Quince</div>
    <div class="divider"></div>
    <ul class="contact-list">
      <li>
        <svg viewBox="0 0 24 24" aria-hidden="true"><path d="M6.6 10.8c1.4 2.8 3.8 5.1 6.6 6.6l2.2-2.2c.3-.3.7-.4 1-.2 1.1.4 2.3.6 3.6.6.6 0 1 .4 1 1V20c0 .6-.4 1-1 1C10.6 21 3 13.4 3 4c0-.6.4-1 1-1h3.5c.6 0 1 .4 1 1 0 1.3.2 2.5.6 3.6.1.3 0 .7-.2 1z"/></svg>
        555-014-2278
      </li>
      <li>
        <svg viewBox="0 0 24 24" aria-hidden="true"><path d="M7 1h10c1.1 0 2 .9 2 2v18c0 1.1-.9 2-2 2H7c-1.1 0-2-.9-2-2V3c0-1.1.9-2 2-2zm0 4v12h10V5H7zm5 14.2a1.2 1.2 0 100 2.4 1.2 1.2 0 000-2.4z"/></svg>
        555-014-2278
      </li>
      <li>
        <svg viewBox="0 0 24 24" aria-hidden="true"><path d="M2 5h20v14H2V5zm2 2v.5l8 5 8-5V7H4zm0 2.9V17h16V9.9l-8 5-8-5z"/></svg>
        info@marlowquince.com
      </li>
      <li>
        <svg viewBox="0 0 24 24" aria-hidden="true"><path d="M12 2a10 10 0 100 20 10 10 0 000-20zm6.9 9h-3c-.1-2.4-.6-4.6-1.4-6.1A8 8 0 0118.9 11zM12 4c.9 1 1.8 3.6 1.9 7h-3.8C10.2 7.6 11.1 5 12 4zM9.5 4.9C8.7 6.4 8.2 8.6 8.1 11h-3a8 8 0 014.4-6.1zM5.1 13h3c.1 2.4.6 4.6 1.4 6.1A8 8 0 015.1 13zM12 20c-.9-1-1.8-3.6-1.9-7h3.8c-.1 3.4-1 6-1.9 7zm2.5-.9c.8-1.5 1.3-3.7 1.4-6.1h3a8 8 0 01-4.4 6.1z"/></svg>
        www.marlowquince.com
      </li>
    </ul>
    <div class="name-band"><span class="person">Your name,</span><span class="title">Title</span></div>
    <p class="address">Street Name, City Name, State Zip Code</p>
  </section>

  <section class="card card-back" aria-label="Card back">
    <div class="monogram"><span>M &amp; Q</span></div>
    <p class="site">www.marlowquince.com</p>
  </section>
</main>
</body>
</html>
```